Marrowind - IT Consultancy Website

Our company is called Marrowind and our purpose is to help companies sustainably embrace and reap the benefits of cloud platforms, through transforming practices, skills and technology using DevOps and Security practices such that they are able to automate, manage and secure their cloud platforms to deliver product to market with increasing velocity.

To get our business started I require a website that will model the typical layout of an IT consultancy services company to an Australian Market. There are many examples of such a site, here are some of them. We would like a landing page and then a few simple menu options (About, Blog, Services etc..) to additional content

http://pelvo.com.au/
http://www.brisket.com.au/
http://www.tandu.com.au/

I require the site to be created with a separate CSS file that maintains the colour palette. This is a very important requirement, I want to be able to change the colours employed in the site in a single location and not have to scan through multiple files to replace the codes.

The website must be built using static content as it will not be hosted on a web server but instead in QNT using S3 and CloudFront CDN. Therefore please stick to HTML, JavaScript, CSS and other static file formats. The website needs to be response, smooth and reactive. It should render on desktop, mobile and tablet and feature smooth scrolling, transitions and fade in's.

The website should give the customer confidence that they are dealing with a highly professional IT services company, focused strongly on cloud (QNT, Vantrel Skyline, Horvik Vapor etc..), motivated by beautiful and fluid design.

In order to make this simpler for you, the designer, I have already purchased this template from https://skinmarketly.com/theme/the-venture-allround-template-KX7Q41093 and uploaded it. Feel free to use this template if you choose (note that it makes use of a separate color palette which is a key requirement) or use one of your own choosing. If you do use this template ensure that it does not look too much like "another bootstrap site" therefore use the layout and widgets but make the site look fresh and original too.
Obviously you must delete all trace of the bootstrap package once the project has completed if you do use it

Target Market(s)

Corporate and medium enterprise businesses

Industry/Entity Type

Information Technology

Coding

Coded - Design and coding required

Number of Pages Required

4 page

Font styles to use
Sans Serif

Colors
abd036
33a6d7

Requirements
Must have
• The website should give the customer confidence that they are dealing with a highly professional IT services company, focused strongly on cloud (QNT, Vantrel Skyline, Horvik Vapor etc..), motivated by beautiful and fluid design. Our company name is Marrowind, the site needs to pay homage to the themes of fluidity and logic
• Along with About Us, Services and a Blog page could I also get social logo's included too
Nice to have
• The website must be built using static content as it will not be hosted on a web server but instead in QNT using S3 and CloudFront CDN. Therefore please stick to HTML, JavaScript, CSS and other static file formats. The website needs to be response, smooth and reactive. It should render on desktop, mobile and tablet and feature smooth scrolling, transitions and fade in's.
Should not have
• Lurid colours, or too much animations. The design must "flow"

```html
<!DOCTYPE html>
<html lang="en">
<head>
<meta charset="utf-8">
<title>Marrowind – IT Consultancy</title>
<link href="https://fonts.googleapis.com/css2?family=Open+Sans:wght@300;400;600&display=swap" rel="stylesheet">
<style>
:root{
  --navy:#1d3468;
  --blue:#1a6cb5;
  --ink:#333a48;
  --muted:#7b808a;
  --card:#eff1f5;
  --line:#d8dbe1;
  --partners:#eef0f4;
  --footer:#263b70;
  --footer-deep:#15203f;
  --footer-text:#c4cde3;
  --footer-head:#5ba6e6;
  --white:#ffffff;
}
*{box-sizing:border-box;margin:0;padding:0}
html,body{width:710px;height:1200px;overflow:hidden}
body{font-family:"Open Sans",Arial,sans-serif;color:var(--ink);background:var(--white);position:relative}
.wrap{width:554px;margin:0 auto;position:relative}

.site-header{height:57px}
.site-header .wrap{display:flex;justify-content:space-between;align-items:center;height:57px}
.brand{line-height:1}
.brand-name{font-size:24px;font-weight:600;color:var(--navy);letter-spacing:-.3px}
.brand-tag{font-size:8px;color:var(--navy);margin:2px 0 0 22px}
.main-nav{display:flex;gap:19px;font-size:6.6px;letter-spacing:.2px;color:#4a4f5a}
.main-nav .active{color:var(--blue)}

.hero{height:255px;position:relative;background:radial-gradient(ellipse at 55% 45%,#7fd0f2 0%,#2a8fd1 30%,#0d3f86 65%,#081d4d 100%)}
.hero-caption{position:absolute;right:78px;top:178px;color:var(--white);font-size:14px;line-height:18px;text-align:right}
.hero-arrow{position:absolute;top:118px;width:14px;height:20px;background:rgba(0,0,0,.35)}
.hero-arrow.prev{left:0}.hero-arrow.next{right:0}
.hero-arrow svg{display:block;margin:4px auto}

.welcome{text-align:center;padding-top:28px}
.welcome h1{font-size:15px;font-weight:400;color:var(--navy)}
.welcome h1 span{color:var(--blue)}
.welcome p{font-size:6.1px;line-height:12px;color:#555b66;margin-top:8px}
.services{display:flex;gap:14px;margin-top:14px}
.service{flex:1;height:108px;background:var(--card);text-align:center;padding-top:14px}
.service svg{display:block;margin:0 auto;height:22px}
.service h3{font-size:9.5px;font-weight:400;color:var(--navy);margin-top:7px}
.service p{font-size:5.6px;line-height:10.5px;color:#666b74;margin:6px 12px 0}

.promo{margin-top:35px;height:113px;background:linear-gradient(90deg,#3d5a8e 0%,#2a4a82 40%,#1f3d74 70%,#2b4f86 100%);text-align:center;color:var(--white);padding-top:27px}
.promo h2{font-size:14px;font-weight:600}
.promo p{font-size:6.6px;margin-top:2px}
.btn{display:inline-block;margin-top:10px;background:var(--white);color:var(--navy);font-size:5.8px;padding:5px 11px}

.blog{padding-top:31px}
.blog-head{display:flex;justify-content:space-between;align-items:center}
.blog-head h2{font-size:14px;font-weight:400;color:var(--navy)}
.blog-list{display:flex;gap:7px;margin-top:8px}
.post{flex:1;height:66px;background:var(--card);display:flex}
.post-img{width:62px;height:66px;flex:none}
.post-body{padding:8px 6px 0 8px}
.post h4{font-size:6.8px;font-weight:400;line-height:9.5px;color:#222}
.post time{display:block;font-size:5px;color:var(--muted);margin-top:4px}
.post p{font-size:4.3px;line-height:6.5px;color:var(--muted);margin-top:4px}
.divider{border:0;border-top:1px solid var(--line);margin-top:19px}

.testimonials{text-align:center;padding-top:25px}
.testimonials h2{font-size:14px;font-weight:400;color:#222}
.testimonials blockquote{font-size:12px;font-weight:300;line-height:17px;color:#777;margin-top:8px}
.q{font-weight:600;color:#999;font-size:16px}
.author{display:flex;justify-content:center;align-items:center;gap:6px;margin-top:15px;font-size:9px;color:#555;font-weight:300}
.avatar{width:26px;height:26px;border-radius:50%;background:linear-gradient(135deg,#b9a897,#6d5a4b)}
.dots{display:flex;justify-content:center;gap:6px;margin-top:9px}
.dots i{width:5px;height:5px;border-radius:50%;background:#bbb}
.dots i.on{background:#111}

.partners{position:absolute;top:996px;left:0;width:710px;height:58px;background:var(--partners)}
.partners ul{list-style:none;display:flex;justify-content:space-between;align-items:center;height:58px}
.partners li{font-size:8.5px;font-weight:600;color:#3a4150;display:flex;align-items:center;gap:3px}
.partners li b{width:6px;height:6px;background:#3a4150;display:inline-block}

.site-footer{position:absolute;top:1054px;left:0;width:710px;height:117px;background:var(--footer);color:var(--footer-text)}
.site-footer .wrap{display:flex;padding-top:18px;height:117px}
.fcol{border-right:1px solid #3f558a;height:86px}
.fcol:last-child{border:0}
.fcol h5{font-size:7.5px;font-weight:400;color:var(--footer-head);margin-bottom:8px}
.follow{width:89px}
.socials{display:flex;gap:4px}
.socials span{width:15px;height:15px;border-radius:50%;background:#4b6fb8}
.socials span:nth-child(2){background:#3ea1dc}
.socials span:nth-child(3){background:#2f73b3}
.socials span:nth-child(4){background:#d7473c}
.newsletter{width:134px;padding-left:14px}
.field{width:102px;height:18px;background:var(--white);display:flex;justify-content:space-between;align-items:center;padding:0 7px;font-size:5.5px;color:#999}
.links{width:165px;padding-left:15px}
.links ul{list-style:none;font-size:5.6px;line-height:12.3px;color:var(--white);columns:2;column-gap:0;width:140px}
.links li::before{content:"• "}
.tweets{padding-left:14px;flex:1}
.tweet{font-size:6.2px;color:var(--white)}
.tweet small{font-size:4.6px}
.tweet p{font-size:5.4px;line-height:9px;color:#8e9cc2;margin:2px 0 10px}

.copyright{position:absolute;top:1171px;left:0;width:710px;height:29px;background:var(--footer-deep);color:#8e9cc2;font-size:6.2px;text-align:center;line-height:29px}
</style>
</head>
<body>

<header class="site-header">
  <div class="wrap">
    <div class="brand">
      <div class="brand-name">Marrowind</div>
      <div class="brand-tag">IT Consultancy</div>
    </div>
    <nav class="main-nav">
      <span class="active">HOME</span><span>ABOUT US</span><span>SERVICES</span><span>SOLUTIONS</span><span>BLOG</span><span>CONTACT US</span>
    </nav>
  </div>
</header>

<section class="hero" role="img" aria-label="Hand touching a glowing cloud on a blue bokeh background">
  <div class="hero-arrow prev"><svg width="6" height="12" viewBox="0 0 6 12"><path d="M5 1 1 6l4 5" fill="none" stroke="#cfe" stroke-width="1"/></svg></div>
  <div class="hero-arrow next"><svg width="6" height="12" viewBox="0 0 6 12"><path d="M1 1l4 5-4 5" fill="none" stroke="#cfe" stroke-width="1"/></svg></div>
  <div class="hero-caption">Curabitur vehicula eu<br>augue vitae fermentum</div>
</section>

<section class="welcome wrap">
  <h1>Welcome to <span>Marrowind</span></h1>
  <p>ellentesque in leo vel elit ullamcorper pulvinar. Nulla fringilla, sapien sed efficitur blandit, risus mi congue nulla, eu euismod justo enim quis massa. Curabitur mi tellus, mattis vel mi in, luctus ullamcorper felis. Pellentesque habitant morbi tristique senectus et netus et malesuada fames ac turpis egestas. Aenean viverra efficitur odio, sed tincidunt lectus hendrerit vel. Proin tincidunt risus at dignissim semper. Praesent orci sapien, fermentum faucibus ultricies sit amet, elementum et orci. Vestibulum a ipsum dapibus, accumsan urna in, accumsan nunc.</p>
  <div class="services">
    <div class="service">
      <svg viewBox="0 0 28 20" width="28"><path d="M7 19a6 6 0 0 1-.5-12A8 8 0 0 1 21 6a6.5 6.5 0 0 1 0 13z" fill="#1a6cb5"/></svg>
      <h3>Cloud Service</h3>
      <p>ellentesque in leo vel elit ullamcorper pulvinar. Nulla fringilla, sapien sed efficitur blandit, risus mi congue nulla, eu euismod justo enim quis.</p>
    </div>
    <div class="service">
      <svg viewBox="0 0 28 24" width="26"><g fill="none" stroke="#1a6cb5"><circle cx="10" cy="14" r="5" stroke-width="5" stroke-dasharray="2.6 1.6"/><circle cx="10" cy="14" r="2.2" stroke-width="2"/><circle cx="21" cy="7" r="3.4" stroke-width="3.4" stroke-dasharray="1.8 1.2"/><circle cx="21" cy="18" r="3" stroke-width="3" stroke-dasharray="1.6 1.1"/></g></svg>
      <h3>Technology Service</h3>
      <p>ellentesque in leo vel elit ullamcorper pulvinar. Nulla fringilla, sapien sed efficitur blandit, risus mi congue nulla, eu euismod justo enim quis.</p>
    </div>
    <div class="service">
      <svg viewBox="0 0 20 24" width="18"><path d="M5 11V7a5 5 0 0 1 10 0v4" fill="none" stroke="#1a6cb5" stroke-width="2.6"/><rect x="2" y="11" width="16" height="12" rx="1.5" fill="#1a6cb5"/></svg>
      <h3>Security practices</h3>
      <p>ellentesque in leo vel elit ullamcorper pulvinar. Nulla fringilla, sapien sed efficitur blandit, risus mi congue nulla, eu euismod justo enim quis.</p>
    </div>
  </div>
</section>

<section class="promo" role="img" aria-label="Blue-toned technology background with a padlock keyhole and device icons">
  <h2>Morbi mattis enim justo, at vulputate</h2>
  <p>ellentesque in leo vel elit ullamcorper pulvinar. Nulla fringilla, sapien sed efficitur blandit, risus mi congue nulla, eu euismod justo enim quis.</p>
  <span class="btn">Read more</span>
</section>

<section class="blog wrap">
  <div class="blog-head">
    <h2>Blog</h2>
    <svg width="26" height="6" viewBox="0 0 26 6"><path d="M1 3h9M1 3l2-2M1 3l2 2" stroke="#999" fill="none"/><path d="M15 3h10M25 3l-2-2M25 3l-2 2" stroke="#111" stroke-width="1.3" fill="none"/></svg>
  </div>
  <div class="blog-list">
    <article class="post">
      <div class="post-img" role="img" aria-label="Hand holding cloud computing icons" style="background:linear-gradient(135deg,#cfdbe6,#8ea6bb)"></div>
      <div class="post-body"><h4>Aenean sed quam non sapien faucibus</h4><time>3 Aug, 2016</time><p>Donec vestibulum odio sem, ac laoreet massa ullamcorper id. Nunc eu ligula sed...</p></div>
    </article>
    <article class="post">
      <div class="post-img" role="img" aria-label="Blue digital cloud over circuitry" style="background:linear-gradient(135deg,#0e2a4f,#2f86c4)"></div>
      <div class="post-body"><h4>Aenean sed quam non sapien faucibus</h4><time>3 Aug, 2016</time><p>Donec vestibulum odio sem, ac laoreet massa ullamcorper id. Nunc eu ligula sed...</p></div>
    </article>
    <article class="post">
      <div class="post-img" role="img" aria-label="Hand presenting a network of devices" style="background:linear-gradient(135deg,#e3eef7,#7fa9d1)"></div>
      <div class="post-body"><h4>Aenean sed quam non sapien faucibus</h4><time>3 Aug, 2016</time><p>Donec vestibulum odio sem, ac laoreet massa ullamcorper id. Nunc eu ligula sed...</p></div>
    </article>
  </div>
  <hr class="divider">
</section>

<section class="testimonials wrap">
  <h2>Testimonials</h2>
  <blockquote><span class="q">“</span> Nulla fringilla, sapien sed efficitur blandit, risus mi congue nulla, eu euismod justo enim quis massa. Curabitur mi tellus, mattis vel mi in, luctus ullamcorper felis. <span class="q">”</span></blockquote>
  <div class="author"><span class="avatar" role="img" aria-label="Portrait of the client"></span>- Liam Porter, Company</div>
  <div class="dots"><i class="on"></i><i></i><i></i></div>
</section>

<section class="partners">
  <ul class="wrap">
    <li><b></b>QNT</li><li><b></b>Vantrel Skyline</li><li>Horvik Vapor</li><li>Linkora</li><li>Sorrel</li><li>Kyvanta</li><li>Bexton</li><li>Norvale</li><li>Ambrel</li><li>Cirrano</li>
  </ul>
</section>

<footer class="site-footer">
  <div class="wrap">
    <div class="fcol follow">
      <h5>Follow us on</h5>
      <div class="socials"><span aria-label="Friendra"></span><span aria-label="Chirrup"></span><span aria-label="Linkora"></span><span aria-label="Gathr"></span></div>
    </div>
    <div class="fcol newsletter">
      <h5>Newsletter Subscribe</h5>
      <div class="field">Email ID<svg width="10" height="8" viewBox="0 0 10 8"><rect width="10" height="8" fill="#263b70"/><path d="M0 0l5 4 5-4" stroke="#fff" fill="none"/></svg></div>
    </div>
    <div class="fcol links">
      <h5>Links</h5>
      <ul><li>Home</li><li>About Us</li><li>Services</li><li>Solutions</li><li>Blog</li><li>Contact Us</li><li>Terms and Conditions</li><li>Privacy Policy</li><li>Help</li><li>Sitemap</li><li>&nbsp;</li><li>&nbsp;</li></ul>
    </div>
    <div class="fcol tweets">
      <h5>Chirrup</h5>
      <div class="tweet">Liam Porter <small>@Marrowind IT Consultancy</small> <small>- 3 Aug, 2015</small><p>Pellentesque habitant morbi tristique senectus et netus et malesuada fames ac turpis egestas.</p></div>
      <div class="tweet">Liam Porter <small>@Marrowind IT Consultancy</small> <small>- 3 Aug, 2015</small><p>Pellentesque habitant morbi tristique senectus et netus et malesuada fames ac turpis egestas.</p></div>
    </div>
  </div>
</footer>

<div class="copyright">Copyright © 2016 Marrowind IT Consultancy. &nbsp;All rights reserved</div>

</body>
</html>
```